The Plate Compass

Cutting Through the Noise to What Actually Works.

Nutrition book

Target Market(s)

People looking to be or get healthy and eat right.

```html
<!DOCTYPE html>
<html lang="en">
<head>
<meta charset="utf-8">
<title>The Plate Compass — Cover</title>
<link href="https://fonts.googleapis.com/css2?family=Roboto+Slab:wght@800&family=Oswald:wght@500;600;700&display=swap" rel="stylesheet">
<style>
  :root{
    --backdrop:#e9eaec;
    --navy:#13264a;
    --cream:#f3ead2;
    --gold:#d99a3a;
    --noise:#8b9098;
    --supplements:#7ea3c4;
    --timing:#3f8196;
    --quality:#85a68f;
    --protein:#e39a3e;
    --calories:#c6562f;
    --rule:#5a6f93;
  }
  *{margin:0;padding:0;box-sizing:border-box}
  html,body{width:1200px;height:1014px;overflow:hidden;background:var(--backdrop)}
  .cover{
    position:absolute;left:300px;top:57px;width:600px;height:900px;
    background:var(--navy);overflow:hidden;
  }
  .title{
    position:absolute;left:0;right:0;top:40px;text-align:center;
    font-family:"Roboto Slab",serif;font-weight:800;color:var(--cream);
    text-transform:uppercase;line-height:.95;
  }
  .title-line{display:flex;justify-content:center;align-items:center;font-size:88px;letter-spacing:1px}
  .title-the{
    font-size:24px;writing-mode:vertical-rl;transform:rotate(180deg);
    margin-right:8px;letter-spacing:2px;
  }
  .subtitle{
    position:absolute;left:40px;right:40px;top:248px;text-align:center;
    font-family:"Oswald",sans-serif;font-weight:600;font-size:28px;line-height:1.15;
    color:var(--gold);text-transform:uppercase;letter-spacing:1px;
  }
  .tier{
    position:absolute;display:flex;align-items:center;justify-content:center;
    font-family:"Oswald",sans-serif;font-weight:600;color:var(--cream);
    text-transform:uppercase;letter-spacing:1px;
    border-top:8px solid rgba(255,255,255,.22);
    box-shadow:0 4px 0 rgba(0,0,0,.25);
  }
  .tier-noise{left:255px;top:390px;width:90px;height:36px;background:var(--noise);font-size:16px;color:#dfe1e4;border-top-width:4px}
  .tier-noise svg{position:absolute;inset:0}
  .tier-supplements{left:200px;top:432px;width:200px;height:58px;background:var(--supplements);font-size:24px}
  .tier-timing{left:163px;top:494px;width:274px;height:62px;background:var(--timing);font-size:32px}
  .tier-quality{left:128px;top:560px;width:344px;height:80px;background:var(--quality);font-size:40px}
  .tier-protein{left:86px;top:644px;width:428px;height:74px;background:var(--protein);font-size:42px}
  .tier-calories{left:44px;top:722px;width:512px;height:88px;background:var(--calories);font-size:52px}
  .most-important{
    position:absolute;left:14px;top:50%;transform:translateY(-40%);
    display:flex;align-items:center;gap:4px;
    font-size:11px;line-height:1.05;letter-spacing:0;color:var(--gold);font-weight:500;text-align:left;
  }
  .rules{position:absolute;left:40px;right:40px;top:832px;height:7px;border-top:2px solid var(--rule);border-bottom:2px solid var(--rule)}
  .author{
    position:absolute;left:0;right:0;top:850px;text-align:center;
    font-family:"Oswald",sans-serif;font-weight:600;font-size:26px;color:var(--cream);
    letter-spacing:2px;text-transform:uppercase;
  }
</style>
</head>
<body>
  <main class="cover">
    <h1 class="title">
      <span class="title-line"><span class="title-the">The</span>Plate</span>
      <span class="title-line">Compass</span>
    </h1>
    <p class="subtitle">Cutting through the noise<br>to what actually works.</p>

    <div class="tier tier-noise">Noise
      <svg width="90" height="32" viewBox="0 0 90 32" aria-hidden="true"><path d="M28 4 L62 28 M62 4 L28 28" stroke="#3b3f46" stroke-width="3"/></svg>
    </div>
    <div class="tier tier-supplements">Supplements</div>
    <div class="tier tier-timing">Meal Timing</div>
    <div class="tier tier-quality">Food Quality</div>
    <div class="tier tier-protein">Protein</div>
    <div class="tier tier-calories">
      <span class="most-important">
        <svg width="8" height="22" viewBox="0 0 8 22" aria-hidden="true"><path d="M4 21 V2 M1 6 L4 1 L7 6" stroke="currentColor" stroke-width="1.5" fill="none"/></svg>
        Most<br>Important
      </span>
      Calories
    </div>

    <div class="rules"></div>
    <p class="author">Dr. Elena Brooks, PhD</p>
  </main>
</body>
</html>
```